Norvane Website Design (New Start Up Investment Management Firm)

We need a website designed. We have attached a Powerpoint with our proposed website content (which is quite minimal), the format is just a suggestion but we would like to see your alternative and improved ideas. We are a boutique investment firm so are looking for something sleek and professional. I have included on the last page of the attachment our brand colours and font styles as well as attaching our logo design. We would like the successful designer to design the website and build the buttons etc.

On the "Contact Us" page, we are open to suggestions on how best to show the map, whether is should be static or open a google maps page. We would like the phone number and email address to be set up so people can click on them on their phone and it calls us or emails us directly.

We would prefer not to have photos of landscapes on the site.
Our website is hosted on a Linux based website.

We would also like 3 links at the bottom of each page for links to pdfs:
- Disclaimer, Terms and Conditions of Web Site Use
- Stewardship
- Pillar III

Target Market(s)

Institutional Investors

Industry/Entity Type

Investment

Coding

Coded - Design and coding required

Number of Pages Required

3 page

Font styles to use
Other font styles liked:
• Logo: Lato, Text: Source Sans Pro

Colors

Designer to choose colors to be used in the design.

Requirements
Must have
• The website must use the colours and fonts on the last page of the attached powerpoint. I can't see an option to select the exact colour palette below so please look at the PPT.
• For others please see Project description.
Should not have
• Landscape photos

```html
<!DOCTYPE html>
<html lang="en">
<head>
<meta charset="utf-8">
<title>Norvane – Contact Us</title>
<link href="https://fonts.googleapis.com/css2?family=Lato:wght@400;700&display=swap" rel="stylesheet">
<style>
  :root {
    --navy: #0d2d5e;
    --nav-text: #1f3f6e;
    --accent: #4a8ad4;
    --body-text: #1c3560;
    --icon: #5b8fd0;
    --footer-text: #ffffff;
    --map-fill: #e6e1d3;
    --bg-light: #f4f5f6;
    --bg-blue: #b9c8da;
  }
  * { margin: 0; padding: 0; box-sizing: border-box; }
  html, body { width: 1200px; height: 755px; overflow: hidden; }
  body { font-family: "Lato", sans-serif; position: relative; background: var(--bg-light); }

  .hero-backdrop {
    position: absolute; left: 0; top: 0; width: 1200px; height: 632px;
    background: linear-gradient(100deg, #f6f6f6 0%, #eef0f2 40%, #c9d5e3 70%, var(--bg-blue) 100%);
  }

  .site-header { position: absolute; left: 0; top: 0; width: 1200px; height: 120px; }
  .brand { position: absolute; left: 120px; top: 28px; display: flex; align-items: center; gap: 14px; }
  .brand-mark { width: 58px; height: 58px; background: var(--navy); }
  .brand-name { font-size: 50px; font-weight: 700; color: var(--navy); letter-spacing: 1px; line-height: 1; }

  .main-nav { position: absolute; top: 47px; left: 617px; display: flex; gap: 43px; }
  .main-nav a { font-size: 17px; color: var(--nav-text); text-decoration: none; letter-spacing: 0.2px; }
  .main-nav a.is-active { color: var(--accent); }

  .page-title {
    position: absolute; top: 164px; left: 0; width: 1200px; text-align: center;
    font-size: 41px; font-weight: 400; color: var(--accent); letter-spacing: 0.5px;
  }

  .location-map {
    position: absolute; left: 209px; top: 259px; width: 343px; height: 280px;
    background: linear-gradient(135deg, #e9e6dc 0%, var(--map-fill) 55%, #d9d6cf 100%);
  }

  .contact-card { position: absolute; left: 617px; top: 272px; color: var(--body-text); font-size: 17px; }
  .contact-card .company { margin-bottom: 8px; }
  .contact-line { display: flex; align-items: flex-start; gap: 6px; line-height: 31px; }
  .contact-line svg { flex: none; margin-top: 7px; }
  .contact-line a { color: var(--body-text); text-decoration: none; }

  .site-footer { position: absolute; left: 0; top: 632px; width: 1200px; height: 123px; background: var(--navy); color: var(--footer-text); }
  .footer-links { position: absolute; left: 123px; top: 28px; font-size: 17px; display: flex; gap: 12px; }
  .footer-links a { color: var(--footer-text); text-decoration: none; }
  .copyright { position: absolute; left: 123px; top: 63px; font-size: 14px; }
  .social-links { position: absolute; left: 887px; top: 33px; display: flex; gap: 6px; }
  .social-links a { width: 35px; height: 35px; border: 1.5px solid var(--footer-text); border-radius: 50%; display: block; }
</style>
</head>
<body>
  <div class="hero-backdrop" role="img" aria-label="Faded photo of a businessman with a city skyline and rising chart overlay"></div>

  <header class="site-header">
    <div class="brand">
      <span class="brand-mark"></span>
      <span class="brand-name">NORVANE</span>
    </div>
    <nav class="main-nav">
      <a href="#">HOME</a>
      <a href="#">ABOUT US</a>
      <a href="#">APPROACH</a>
      <a href="#" class="is-active">CONTACT US</a>
    </nav>
  </header>

  <h1 class="page-title">CONTACT US</h1>

  <div class="location-map" role="img" aria-label="Street map showing the office location near the station"></div>

  <section class="contact-card">
    <p class="company">NORVANE</p>
    <div class="contact-line">
      <svg width="18" height="22" viewBox="0 0 18 22"><path d="M9 1C5 1 2 4 2 8c0 5 7 13 7 13s7-8 7-13c0-4-3-7-7-7z" fill="var(--icon)"/><circle cx="9" cy="8" r="2.6" fill="#fff"/></svg>
      <span>14 Harrowgate Row London W1 4QT<br>United Kingdom</span>
    </div>
    <div class="contact-line">
      <svg width="20" height="18" viewBox="0 0 20 18"><path d="M4 1l3 3-2 3c1 2 3 4 5 5l3-2 3 3-2 3C8 16 3 11 1 4z" fill="none" stroke="var(--icon)" stroke-width="1.4" stroke-linejoin="round"/></svg>
      <a href="tel:+442079460318">T: +44 20 7946 0318</a>
    </div>
    <div class="contact-line">
      <svg width="20" height="16" viewBox="0 0 20 16"><rect x="1" y="1" width="18" height="13" fill="none" stroke="var(--icon)" stroke-width="1.4"/><path d="M1 1l9 7 9-7" fill="none" stroke="var(--icon)" stroke-width="1.4"/></svg>
      <a href="mailto:clientservices@norvaneim.com">E: clientservices@norvaneim.com</a>
    </div>
  </section>

  <footer class="site-footer">
    <nav class="footer-links">
      <a href="#">Disclaimer</a><span>|</span>
      <a href="#">Terms and Conditions</a><span>|</span>
      <a href="#">Stewardship</a><span>|</span>
      <a href="#">Pillar III</a>
    </nav>
    <p class="copyright">© 2017 Company Name&nbsp; All right reserved&nbsp; Term of Use</p>
    <div class="social-links">
      <a href="#" aria-label="Social profile 1"></a>
      <a href="#" aria-label="Social profile 2"></a>
      <a href="#" aria-label="Social profile 3"></a>
      <a href="#" aria-label="Social profile 4"></a>
      <a href="#" aria-label="Social profile 5"></a>
    </div>
  </footer>
</body>
</html>
```